Website for research group at university relating to human wildlife conflict

Australian university based research group. Researching the relationship between humans and wildlife, and seeking to explore ways for the two to coexist. The research group is called "Creature Harmony NexaForm lab" (NexaForm=coexistence, which should be spelled out somewhere)

I have a logo for the research group (from artflockly). it is attached. I like it when the logo can be used throughout the website (e.g for titles, and in backgrounds).

Just a simple and clean/modern feel. i like the following websites as examples, but also like to be a little different!
https://www.feralvantis.org/
http://www.qmbrn.org/

At least one large image on each page, like a banner (just put in one and i can replace them). Images of Australian wildlife preferred (especially canids), and images with humans and animals helps too.

I would like the following pages
Home page (including Vision statement; and link to twitter account).
THEN, the following pages- which can all be the same/similar design with minor differences according to content of that page.
People (inc photo and profile)
Publications (list of publications by topic)
Projects (details of projects- with title, photo, detail)
News items (by topic, with title, image, link)
Contact
Collaborators (list of groups and people we associated with group- name and photo)

Target Market(s)

government. researchers. university.

Industry/Entity Type

University

Coding

Coded - Design and coding required

Number of Pages Required

5+ page

Font styles to use
Sans Serif

Colors

Designer to choose colors to be used in the design.

Requirements
Must have
• I require all the coded files so that i have flexibility of where i can host it.
• must have my logo.
• must have a visually appealing, modern and easy to navigate landing page.
• must have a large photo (e.g banner) at the top of every page.
• must have twitter feed on home page.
Nice to have
• I require all the coded files so that i have the flexibility of where i can host it.

```html
<!DOCTYPE html>
<html lang="en">
<head>
<meta charset="utf-8">
<title>Creature Harmony NexaForm lab</title>
<link href="https://fonts.googleapis.com/css2?family=Montserrat:wght@400;500;600;700&family=Mulish:wght@400;600;700&display=swap" rel="stylesheet">
<style>
:root{
  --orange:#e9581f;
  --green:#4b6b24;
  --green-dark:#3f5c1d;
  --bg:#f1f1f1;
  --white:#ffffff;
  --ink:#2b2b2b;
  --text:#3a3a3a;
  --nav:#2a4f66;
}
*{margin:0;padding:0;box-sizing:border-box}
html,body{width:1200px;height:3564px;overflow:hidden}
body{position:relative;background:var(--bg);font-family:"Mulish",sans-serif;color:var(--text)}
.abs{position:absolute}

/* top bar */
.topbar{left:0;top:0;width:1200px;height:43px;background:var(--orange);color:var(--white);font-size:14px;font-family:"Montserrat",sans-serif}
.topbar .socials{left:116px;top:13px;display:flex;gap:12px}
.topbar .socials span{width:16px;height:16px;border-radius:50%;border:1.5px solid var(--white);display:block}
.topbar .contact-info{right:104px;top:12px;display:flex;gap:16px;align-items:center}
.topbar .contact-info span{display:flex;align-items:center;gap:6px}
.topbar .divider{width:1px;height:18px;background:rgba(255,255,255,.6)}

/* header */
.header{left:0;top:43px;width:1200px;height:109px;background:var(--white)}
.brand{left:100px;top:26px;display:flex;align-items:center;gap:10px}
.brand .dot{width:40px;height:40px;border-radius:50%;background:var(--orange)}
.brand .name{font-family:"Montserrat",sans-serif;font-weight:700;font-size:15px;line-height:18px;color:var(--green);width:120px}
.nav{left:310px;top:30px;display:flex;align-items:center;gap:30px;font-family:"Montserrat",sans-serif;font-size:19px;color:var(--nav)}
.nav .home{width:72px;height:72px;border-radius:50%;border:3px solid var(--green);display:flex;align-items:center;justify-content:center;color:var(--orange);font-size:17px;margin-right:-4px;margin-top:-6px}

/* hero */
.hero{left:0;top:152px;width:1200px;height:660px;
  background:
    radial-gradient(ellipse 240px 380px at 840px 120px,rgba(214,218,180,.75),rgba(214,218,180,0) 70%),
    radial-gradient(ellipse 160px 220px at 560px 330px,#4a4a3c,rgba(74,74,60,0) 75%),
    radial-gradient(ellipse 420px 200px at 620px 640px,#6b6a52,rgba(107,106,82,0) 70%),
    linear-gradient(90deg,#0f150e 0%,#26331f 22%,#3f4d33 48%,#4b5a3c 62%,#26331f 82%,#0f150e 100%)}
.hero-shade{left:0;top:152px;width:1200px;height:660px;background:linear-gradient(180deg,rgba(0,0,0,0) 55%,rgba(0,0,0,.35) 100%)}
.hero-title{left:0;top:500px;width:1200px;text-align:center;color:var(--white);font-family:"Montserrat",sans-serif;font-weight:500;font-size:58px;text-shadow:0 2px 6px rgba(0,0,0,.4)}
.hero-sub{left:0;top:578px;width:1200px;text-align:center;color:var(--white);font-family:"Montserrat",sans-serif;font-weight:500;font-size:24px;line-height:43px;text-shadow:0 2px 6px rgba(0,0,0,.4)}
.hero-curve{left:0;top:680px;width:1200px;height:140px}
.scroll-down{left:570px;top:710px;width:60px;height:60px;border-radius:50%;background:var(--green);display:flex;align-items:center;justify-content:center}

/* about */
.about-title{left:0;top:910px;width:1200px;text-align:center;font-family:"Montserrat",sans-serif;font-weight:700;font-size:36px;color:var(--green)}
.about-title span{color:var(--orange)}
.about-mark{left:555px;top:968px;width:90px;height:90px;border-radius:50%;border:7px solid var(--green)}
.about-shadow{left:560px;top:1050px;width:80px;height:8px;border-radius:50%;background:rgba(0,0,0,.15)}
.about-text{left:200px;top:1078px;width:800px;text-align:justify;text-align-last:center;font-size:18px;line-height:32px;color:var(--text)}
.green-band{left:0;top:1421px;width:1200px;height:398px;background:var(--green)}
.video{left:223px;top:1228px;width:754px;height:381px;
  background:
    radial-gradient(ellipse 220px 300px at 560px 170px,#7a6a4e,rgba(122,106,78,0) 75%),
    radial-gradient(ellipse 120px 60px at 610px 300px,#e8e2cc,rgba(232,226,204,0) 80%),
    radial-gradient(ellipse 260px 200px at 180px 120px,#e2a94a,rgba(226,169,74,0) 75%),
    linear-gradient(110deg,#4d3512 0%,#9c6e2a 30%,#7a5a2c 55%,#3b2c18 100%)}
.play{left:584px;top:1392px;width:32px;height:32px;border-radius:50%;border:2px solid var(--orange);background:rgba(255,255,255,.9);display:flex;align-items:center;justify-content:center}
.band-text{left:150px;top:1644px;width:900px;text-align:justify;text-align-last:center;color:var(--white);font-size:16px;line-height:31px}

/* feature rows */
.feature-img{width:478px;height:333px;box-shadow:0 2px 6px rgba(0,0,0,.25);overflow:hidden}
.corner{width:76px;height:76px;background:var(--white);display:flex;align-items:center;justify-content:center}
.corner.br{border-top-left-radius:76px;right:0;bottom:0;padding:16px 0 0 16px}
.corner.bl{border-top-right-radius:76px;left:0;bottom:0;padding:16px 16px 0 0}
.corner i{width:30px;height:30px;border-radius:50%;border:3px solid var(--green);display:block}
.feature-title{font-family:"Montserrat",sans-serif;font-weight:500;font-size:32px;color:var(--orange)}
.feature-text{width:410px;font-size:16.5px;line-height:31px;text-align:justify;color:var(--text)}
.btn{display:flex;align-items:center;justify-content:center;width:150px;height:40px;background:var(--green);color:var(--white);font-family:"Montserrat",sans-serif;font-weight:700;font-size:16px}

.img-tiger{background:
  radial-gradient(ellipse 120px 150px at 160px 170px,#b5621c,rgba(181,98,28,0) 75%),
  radial-gradient(ellipse 300px 120px at 300px 60px,#f0c070,rgba(240,192,112,0) 75%),
  linear-gradient(180deg,#d89a48 0%,#c27a2c 45%,#9a5a1c 75%,#6f3f14 100%)}
.img-zebra{background:
  radial-gradient(circle 38px at 218px 58px,#fff2b0,#ffd25a 60%,rgba(255,160,40,0) 100%),
  radial-gradient(ellipse 300px 110px at 220px 80px,#f8b030,rgba(248,176,48,0) 80%),
  linear-gradient(180deg,#e88a20 0%,#de6a14 35%,#8a5a36 52%,#5a4632 70%,#c88a4a 88%,#9a6a3a 100%)}
.img-field{background:
  radial-gradient(ellipse 90px 70px at 90px 120px,#6a6a62,rgba(106,106,98,0) 80%),
  radial-gradient(ellipse 70px 55px at 340px 140px,#5e5e58,rgba(94,94,88,0) 80%),
  radial-gradient(ellipse 120px 60px at 210px 140px,#5a7fa8,rgba(90,127,168,0) 80%),
  linear-gradient(180deg,#8c8a88 0%,#7c7a6e 25%,#5a7a3a 48%,#68a03a 72%,#7cb84a 100%)}

/* footer */
.footer-wave{left:0;top:3094px;width:1200px;height:44px}
.footer{left:0;top:3136px;width:1200px;height:338px;background:var(--white)}
.tweet-card{left:102px;top:3188px;width:200px;height:281px;background:var(--white);box-shadow:0 1px 5px rgba(0,0,0,.25);padding:8px;font-size:7px;line-height:10px;color:#555}
.tweet-card .head{display:flex;gap:5px;align-items:center}
.tweet-card .head i{width:18px;height:18px;border-radius:50%;background:var(--orange);display:block;flex:none}
.tweet-card .head b{font-size:7.5px;color:var(--ink)}
.tweet-card p{margin-top:12px}
.tweet-card .tag{color:#3a7bbf}
.tweet-card .pic{margin-top:6px;height:96px;background:radial-gradient(ellipse 50px 70px at 60% 25%,#c8cfb8,rgba(200,207,184,0) 80%),radial-gradient(ellipse 30px 30px at 50% 60%,#4a4a40,rgba(74,74,64,0) 80%),linear-gradient(90deg,#1a2218,#3c4a34 50%,#1a2218)}
.tweet-card .meta{margin-top:6px;color:#999;border-bottom:1px solid #eee;padding-bottom:6px}
.tweet-card .actions{margin-top:8px;display:flex;justify-content:space-around}
.tweet-card .actions span{width:10px;height:10px;border-radius:50%;border:1.5px solid #999;display:block}
.foot-h{font-family:"Montserrat",sans-serif;font-weight:700;font-size:19px;color:var(--ink)}
.contact-list{left:356px;top:3286px;font-size:14px;line-height:21px;color:var(--ink)}
.contact-list li{list-style:none;display:flex;gap:16px;margin-bottom:14px}
.contact-list svg{flex:none;margin-top:2px}
.foot-social{left:356px;top:3410px;display:flex;gap:10px}
.foot-social span{width:30px;height:30px;border-radius:50%;border:1.5px solid #666;display:flex;align-items:center;justify-content:center}
.foot-social span i{width:8px;height:8px;border-radius:50%;background:#666;display:block}
.news-text{left:632px;top:3280px;width:290px;font-size:13.5px;line-height:21px;color:var(--ink)}
.news-input{left:632px;top:3340px;width:275px;height:44px;border:1px solid #bbb;padding:0 14px;display:flex;align-items:center;font-size:12px;color:#777}
.news-btn{left:632px;top:3402px;width:126px;height:38px}
.quick-links{left:980px;top:3276px;font-size:13.5px;line-height:25.5px;color:var(--ink)}
.quick-links li{list-style:none;padding-left:16px;position:relative}
.quick-links li:before{content:"";position:absolute;left:3px;top:9px;border-left:5px solid var(--ink);border-top:4px solid transparent;border-bottom:4px solid transparent}
.copyright-bar{left:0;top:3474px;width:1200px;height:90px;background:var(--white);border-top:1px solid #e2e2e2;text-align:center;font-size:14px;padding-top:34px;color:var(--ink)}
</style>
</head>
<body>

<div class="abs topbar">
  <div class="abs socials" aria-label="Social links"><span></span><span></span><span></span><span></span><span></span><span></span><span></span></div>
  <div class="abs contact-info">
    <span><svg width="14" height="12" viewBox="0 0 14 12"><rect x="0.5" y="0.5" width="13" height="11" fill="none" stroke="#fff"/><path d="M1 1l6 5 6-5" fill="none" stroke="#fff"/></svg>Email us: info@nexaformlab.org</span>
    <span class="divider"></span>
    <span><svg width="13" height="13" viewBox="0 0 24 24"><path fill="#fff" d="M6.6 10.8a15 15 0 006.6 6.6l2.2-2.2a1 1 0 011-.25 11.4 11.4 0 003.6.57 1 1 0 011 1V20a1 1 0 01-1 1A17 17 0 013 4a1 1 0 011-1h3.5a1 1 0 011 1c0 1.25.2 2.45.57 3.57a1 1 0 01-.25 1z"/></svg>Call us: 888 888 8888</span>
  </div>
</div>

<header class="abs header">
  <div class="abs brand"><span class="dot"></span><span class="name">Creature Harmony NexaForm lab</span></div>
  <nav class="abs nav">
    <span class="home">Home</span><span>People</span><span>Publications</span><span>Projects</span><span>News</span><span>Contact</span><span>Collaborators</span>
  </nav>
</header>

<section class="abs hero" role="img" aria-label="Elephant walking along a misty forest track with sunlight streaming through trees"></section>
<div class="abs hero-shade"></div>
<h1 class="abs hero-title">Creature Harmony NexaForm lab</h1>
<p class="abs hero-sub">Sed ut perspiciatis unde omnis iste natus error sit voluptatem accusan<br>et quasi architecto beatae vitae dicta sunt explicabo.</p>
<svg class="abs hero-curve" viewBox="0 0 1200 140" preserveAspectRatio="none">
  <path d="M0 35 Q600 175 1200 35 L1200 140 L0 140 Z" fill="#f1f1f1"/>
  <path d="M0 40 Q600 190 1200 40 Q600 160 0 40 Z" fill="#4b6b24"/>
</svg>
<div class="abs scroll-down"><svg width="22" height="14" viewBox="0 0 22 14"><path d="M3 3l8 8 8-8" fill="none" stroke="#fff" stroke-width="3.5" stroke-linecap="round"/></svg></div>

<h2 class="abs about-title">ABOUT <span>US</span></h2>
<div class="abs about-mark"></div>
<div class="abs about-shadow"></div>
<p class="abs about-text">Sed ut perspiciatis unde omnis iste natus error sit voluptatem accusantium doloremque laudantium, totam rem aperiam, eaque ipsa quae ab illo inventore veritatis et quasi architecto beatae vitae dicta sunt explicabo. Nemo enim ipsam voluptatem quia voluptas sit aspernatur aut odit aut fugit, nesciunt.</p>

<div class="abs green-band"></div>
<div class="abs video" role="img" aria-label="Researcher taking field notes on plant samples in a sunlit forest"></div>
<div class="abs play"><svg width="12" height="12" viewBox="0 0 12 12"><path d="M3 1.5l7 4.5-7 4.5z" fill="none" stroke="#e9581f" stroke-width="1.5"/></svg></div>
<p class="abs band-text">Sed ut perspiciatis unde omnis iste natus error sit voluptatem accusantium doloremque laudantium, totam rem aperiam, eaque ipsa quae ab illo inventore veritatis et quasi architecto beatae vitae dicta sunt explicabo. Nemo enim ipsam voluptatem quia voluptas sit aspernatur aut odit aut fugit, sed quia consequuntur magni dolores eos qui ratione voluptatem sequi nesciunt.</p>

<div class="abs feature-img img-tiger" style="left:102px;top:1891px" role="img" aria-label="Tiger walking through golden grassland">
  <div class="abs corner br"><i></i></div>
</div>
<h3 class="abs feature-title" style="left:660px;top:1938px">OUR MISSION</h3>
<p class="abs feature-text" style="left:660px;top:1988px">At vero eos et accusamus et iusto odio dignissimos ducimus qui blanditiis praesentium voluptatum deleniti atque corrupti quos dolores et quas molestias excepturi expedita distinctio.</p>
<div class="abs btn" style="left:662px;top:2131px">Read More</div>

<h3 class="abs feature-title" style="left:128px;top:2346px">OUR VISSION</h3>
<p class="abs feature-text" style="left:128px;top:2396px">At vero eos et accusamus et iusto odio dignissimos ducimus qui blanditiis praesentium voluptatum deleniti atque corrupti quos dolores et quas molestias excepturi expedita distinctio.</p>
<div class="abs btn" style="left:130px;top:2533px">Read More</div>
<div class="abs feature-img img-zebra" style="left:620px;top:2295px" role="img" aria-label="Herd of zebras on the savanna under a setting sun">
  <div class="abs corner bl"><i></i></div>
</div>

<div class="abs feature-img img-field" style="left:102px;top:2704px" role="img" aria-label="Group of people watching elephants on a green field">
  <div class="abs corner br"><i></i></div>
</div>
<h3 class="abs feature-title" style="left:660px;top:2753px">WHAT WE DO</h3>
<p class="abs feature-text" style="left:660px;top:2802px">At vero eos et accusamus et iusto odio dignissimos ducimus qui blanditiis praesentium voluptatum deleniti atque corrupti quos dolores et quas molestias excepturi expedita distinctio.</p>
<div class="abs btn" style="left:662px;top:2937px">Read More</div>

<svg class="abs footer-wave" viewBox="0 0 1200 44" preserveAspectRatio="none">
  <path d="M0 26 C30 18 50 30 80 24 C110 18 130 10 170 18 C210 26 240 30 280 22 C320 14 350 12 390 22 C430 32 460 26 500 18 C540 10 570 14 610 24 C650 34 690 28 720 20 C760 10 800 14 840 24 C880 32 910 26 950 18 C990 10 1020 16 1060 24 C1100 32 1140 26 1170 18 C1185 14 1195 16 1200 18 L1200 44 L0 44 Z" fill="#fff"/>
</svg>
<footer class="abs footer"></footer>

<div class="abs tweet-card">
  <div class="head"><i></i><div><b>Creature Harmony NexaForm lab</b><br>@nexaformlab</div></div>
  <p>Field notes from our latest camera trap survey, shared for partners and friends across the region. <span class="tag">#NexaForm</span></p>
  <div class="pic" role="img" aria-label="Elephant in a misty forest"></div>
  <div class="meta">9:41 AM · 3 Mar</div>
  <div class="actions"><span></span><span></span><span></span><span></span></div>
</div>

<h4 class="abs foot-h" style="left:356px;top:3224px">CONTACT US</h4>
<ul class="abs contact-list">
  <li><svg width="14" height="18" viewBox="0 0 14 18"><path d="M7 0a7 7 0 00-7 7c0 5 7 11 7 11s7-6 7-11a7 7 0 00-7-7z" fill="#e9581f"/><circle cx="7" cy="7" r="2.5" fill="#fff"/></svg><span>42 Wattle Grove Rd.,<br>Suite # 12, Kestrel Bay, NSW 2000</span></li>
  <li><svg width="14" height="14" viewBox="0 0 24 24"><path fill="#e9581f" d="M6.6 10.8a15 15 0 006.6 6.6l2.2-2.2a1 1 0 011-.25 11.4 11.4 0 003.6.57 1 1 0 011 1V20a1 1 0 01-1 1A17 17 0 013 4a1 1 0 011-1h3.5a1 1 0 011 1c0 1.25.2 2.45.57 3.57a1 1 0 01-.25 1z"/></svg><span>Phone: 888 888 8888</span></li>
  <li><svg width="14" height="12" viewBox="0 0 14 12"><rect width="14" height="11" y="0.5" fill="#e9581f"/><path d="M0.5 1l6.5 5 6.5-5" fill="none" stroke="#fff"/></svg><span>Email: info@nexaformlab.org</span></li>
</ul>
<div class="abs foot-social"><span><i></i></span><span><i></i></span><span><i></i></span></div>

<h4 class="abs foot-h" style="left:632px;top:3224px">SIGN UP FOR NEWSLETTER</h4>
<p class="abs news-text">Want to make an impact? Provide your email and we'll be in touch.</p>
<div class="abs news-input">Enter email</div>
<div class="abs btn news-btn">SIGN UP</div>

<h4 class="abs foot-h" style="left:980px;top:3224px">QUICK LINKS</h4>
<ul class="abs quick-links">
  <li>Home</li><li>People</li><li>Publications</li><li>Projects</li><li>News Items</li><li>Contact</li><li>Collaborators</li>
</ul>

<div class="abs copyright-bar">Copyrights © 2019 All Rights Reserved | Privacy Policy | Terms and Conditions</div>

</body>
</html>
```